New business card for a regional office of a US M&A company

We need business card for a finance company, office based in Hong Kong , our Head office is in US, our business is to Merge and acquires companies , the new office will be a regional office for the Asia Pacific region. We want to use the head office logo as attached ( but don't have to be exactly the same, can be a variation to it) as a base and then add Asia Pacific alongside the logo.
We would prefer to have be bilingual Eng + Chinese, although we don't really have Chinese company name .

Industry/Entity Type

Business

Contact Information for Business Card

Clara Jo Tsang
 

VP,
APAC M&A Operations
ORIN VANTAGE Asia Pacific Limited
 
Unit 1407, K18
18 Tai Lok Shan Road, 
Hong Kong 
 
M: +852 6038 1742
T : +852 2836 4100
F : +852 2836 4177
VOIP: 4158
 
cjtsang@orinvantage.com

Font styles to use
Serif
Sans Serif

Colors

Designer to choose colors to be used in the design.

Requirements
Must have
• APAC Office

```html
<!DOCTYPE html>
<html lang="en">
<head>
<meta charset="utf-8">
<title>Orin Vantage – APAC Business Card</title>
<link href="https://fonts.googleapis.com/css2?family=Open+Sans:wght@700&family=Roboto:wght@400;500&family=Roboto+Condensed:wght@500&display=swap" rel="stylesheet">
<style>
  :root {
    --page-bg: #e9e6e1;
    --card-navy: #0f2843;
    --accent-cyan: #1fa9d0;
    --corner-white: #eef1f4;
    --text-light: #e3e9ef;
    --divider: rgba(255,255,255,0.35);
  }
  html, body {
    margin: 0;
    padding: 0;
    width: 1200px;
    height: 960px;
    overflow: hidden;
    background: var(--page-bg);
  }
  .canvas {
    position: relative;
    width: 1200px;
    height: 960px;
  }
  .card {
    position: absolute;
    width: 600px;
    height: 343px;
    background: var(--card-navy);
    overflow: hidden;
    box-shadow: 0 3px 8px rgba(0,0,0,0.25);
  }
  .card--front { left: 314px; top: 113px; }
  .card--back  { left: 311px; top: 472px; }

  .corner { position: absolute; width: 0; height: 0; }
  .corner--top-left {
    left: 0; top: 0;
    border-top: 50px solid var(--corner-white);
    border-right: 50px solid transparent;
  }
  .corner--bottom-right {
    right: 0; bottom: 0;
    border-bottom: 52px solid var(--accent-cyan);
    border-left: 52px solid transparent;
  }

  .brand-name {
    position: absolute;
    margin: 0;
    font-family: "Open Sans", sans-serif;
    font-weight: 700;
    color: var(--accent-cyan);
    white-space: nowrap;
    text-align: center;
    letter-spacing: 0.5px;
  }
  .card--front .brand-name {
    left: 0; width: 320px;
    top: 196px;
    font-size: 31px;
  }
  .card--back .brand-name {
    left: 0; width: 600px;
    top: 183px;
    font-size: 44px;
  }

  .divider {
    position: absolute;
    left: 319px; top: 52px;
    width: 1px; height: 242px;
    background: linear-gradient(to bottom, transparent, var(--divider) 20%, var(--divider) 80%, transparent);
  }

  .contact {
    position: absolute;
    left: 349px; top: 56px;
    font-family: "Roboto", sans-serif;
    font-size: 14px;
    line-height: 19px;
    color: var(--text-light);
  }
  .contact__name {
    margin: 0;
    font-family: "Roboto Condensed", sans-serif;
    font-weight: 500;
    font-size: 21px;
    line-height: 24px;
    color: var(--accent-cyan);
    text-transform: uppercase;
  }
  .contact__title {
    margin: 2px 0 14px 2px;
    font-weight: 500;
    font-size: 14px;
  }
  .contact__block { margin: 0; }
  .contact__lines { list-style: none; margin: 7px 0 0; padding: 0; }
  .contact__lines li { display: flex; align-items: center; height: 19px; }
  .contact__lines svg { width: 14px; height: 14px; margin-right: 9px; fill: var(--accent-cyan); }
  .contact__voip { margin: 12px 0 0; }

  .website {
    position: absolute;
    left: 0; width: 600px;
    top: 284px;
    margin: 0;
    text-align: center;
    font-family: "Roboto", sans-serif;
    font-size: 14px;
    letter-spacing: 6px;
    color: var(--text-light);
  }
</style>
</head>
<body>
<main class="canvas">

  <section class="card card--front" aria-label="Business card front">
    <span class="corner corner--top-left"></span>
    <span class="corner corner--bottom-right"></span>

    <p class="brand-name">ORIN VANTAGE</p>

    <span class="divider"></span>

    <div class="contact">
      <h1 class="contact__name">Clara Jo Tsang</h1>
      <p class="contact__title">VP</p>
      <p class="contact__block">APAC M&amp;A Operations<br>Orin Vantage Asia Pacific Limited</p>
      <p class="contact__block">Unit 1407, K18<br>18 Tai Lok Shan Road<br>Hong Kong</p>
      <ul class="contact__lines">
        <li>
          <svg viewBox="0 0 24 24" aria-label="Telephone"><path d="M6.6 10.8a15.1 15.1 0 0 0 6.6 6.6l2.2-2.2c.3-.3.7-.4 1-.2 1.1.4 2.3.6 3.6.6.6 0 1 .4 1 1V20c0 .6-.4 1-1 1A17 17 0 0 1 3 4c0-.6.4-1 1-1h3.5c.6 0 1 .4 1 1 0 1.3.2 2.5.6 3.6.1.3 0 .7-.2 1z"/></svg>
          +852 2836 4100
        </li>
        <li>
          <svg viewBox="0 0 24 24" aria-label="Mobile"><path d="M7 1h10a2 2 0 0 1 2 2v18a2 2 0 0 1-2 2H7a2 2 0 0 1-2-2V3a2 2 0 0 1 2-2zm0 3v14h10V4zm5 15.5a1 1 0 1 0 0 2 1 1 0 0 0 0-2z"/></svg>
          +852 6038 1742
        </li>
        <li>
          <svg viewBox="0 0 24 24" aria-label="Fax"><path d="M6 2h12v6H6zM3 9h18a1 1 0 0 1 1 1v8h-4v4H6v-4H2v-8a1 1 0 0 1 1-1zm5 7v4h8v-4z"/></svg>
          +852 2836 4177
        </li>
      </ul>
      <p class="contact__voip">VOIP: 4158</p>
    </div>
  </section>

  <section class="card card--back" aria-label="Business card back">
    <p class="brand-name">ORIN VANTAGE</p>
    <p class="website">www.orinvantage.com</p>
  </section>

</main>
</body>
</html>
```